Healthy lifestyle Influencer business card

I need your creativity to have a business card that I can leave in all the restaurants, hotels and spas I visit to inform them that I am an influencer specializing in the wellness sector and that I will write a review about them. You can use my instagram photos Lunavita27 or on my website www.piattileggeriorto.it. I would like my business card to impress with its creativity! thank you very much!

Contact Information for Business Card

siteweb, instagram, phone number

Font styles to use
Decorative
Script

Colors
0094D4
00A9DD
6FCCEA
C7EBF8
E9F6FB
59FF00
82FF00
B8FF75
E3FFCB
F4FFEA
FFC000
F8CF3A
FAE287
FDF2CF
FEFAEE
F0912C
F2A743
F7CA91
FBE8D2
FDF5EE
EE7325
F08F49
F5BC92
FAE3D3
FDF4ED
EB3D1F
EC4F4E
F09395
F8D3D4
FCEDEE
E54698
E96AAD
F1A4CE
F9D9EA
FCEFF6

Requirements
Nice to have
• creativity

```html
<!DOCTYPE html>
<html lang="it">
<head>
<meta charset="utf-8">
<title>Luna Vita Chef – Biglietto da visita</title>
<link href="https://fonts.googleapis.com/css2?family=Great+Vibes&family=Quicksand:wght@500&family=Roboto:wght@300;400&display=swap" rel="stylesheet">
<style>
  :root {
    --page-bg: #2a2a2a;
    --card-top: #1c1c1c;
    --card-bottom: #2b2b2c;
    --emboss-ink: #0e0e0e;
    --text-light: #e8e8e8;
    --text-soft: #c9c9c9;
    --icon-grey: #9a9a9a;
    --kiwi-green: #8fae3a;
    --kiwi-deep: #6f8a2c;
    --kiwi-brown: #a7804f;
  }
  * { margin: 0; padding: 0; box-sizing: border-box; }
  html, body {
    width: 1200px; height: 1138px; overflow: hidden;
    background: var(--page-bg);
  }
  .card {
    position: absolute; left: 272px; width: 622px; height: 377px;
    border-radius: 16px; overflow: hidden;
    background: linear-gradient(160deg, var(--card-top) 0%, var(--card-bottom) 100%);
  }
  .card--front { top: 183px; }
  .card--back { top: 606px; }

  .brand-name, .tagline {
    position: absolute; white-space: nowrap; text-align: center;
    font-family: "Quicksand", sans-serif; font-weight: 500;
  }
  .card--front .brand-name {
    left: 0; right: 0; top: 150px; line-height: 56px;
    font-size: 50px; color: var(--emboss-ink);
  }
  .card--front .tagline {
    left: 0; right: 0; top: 224px; line-height: 26px;
    font-size: 22px; color: var(--emboss-ink);
  }
  .card--back .brand-name {
    left: 40px; width: 280px; top: 153px; line-height: 40px;
    font-size: 33px; color: var(--text-light);
  }
  .card--back .tagline {
    left: 40px; width: 280px; top: 203px; line-height: 20px;
    font-size: 15px; color: var(--text-light);
  }

  .social {
    position: absolute; left: 0; right: 0; height: 22px;
    display: flex; justify-content: center; align-items: center; gap: 12px;
    font-family: "Roboto", sans-serif; font-weight: 400; font-size: 17px;
    color: var(--text-soft);
  }
  .card--front .social { top: 334px; }
  .card--back .social { top: 327px; }
  .social__dot {
    width: 14px; height: 14px; border-radius: 50%; background: var(--icon-grey);
  }

  .person-name {
    position: absolute; left: 345px; top: 114px; line-height: 40px;
    font-family: "Great Vibes", cursive; font-size: 30px; color: var(--text-light);
  }
  .contact-list {
    position: absolute; left: 352px; top: 158px; list-style: none;
    font-family: "Roboto", sans-serif; font-weight: 300; font-size: 15px;
    color: var(--text-soft);
  }
  .contact-list li { display: flex; align-items: center; height: 21px; gap: 10px; }
  .contact-list svg { width: 13px; height: 13px; fill: var(--icon-grey); }
  .vat-number {
    position: absolute; left: 353px; top: 227px; line-height: 20px;
    font-family: "Roboto", sans-serif; font-weight: 300; font-size: 15px;
    color: var(--text-soft);
  }

  .kiwi-photo { position: absolute; }
  .kiwi-photo--top {
    right: 0; top: 0; width: 118px; height: 134px;
    border-bottom-left-radius: 60% 55%;
    background: radial-gradient(circle at 70% 40%, var(--kiwi-green) 0%, var(--kiwi-deep) 45%, var(--kiwi-brown) 75%, transparent 76%);
  }
  .kiwi-photo--bottom {
    left: 0; bottom: 0; width: 118px; height: 138px;
    border-top-right-radius: 60% 55%;
    background: radial-gradient(circle at 30% 60%, var(--kiwi-green) 0%, var(--kiwi-deep) 45%, var(--kiwi-brown) 75%, transparent 76%);
  }
</style>
</head>
<body>

<section class="card card--front" aria-label="Fronte del biglietto">
  <div class="brand-name">Luna Vita Chef</div>
  <div class="tagline">Sana e felice a ogni assaggio</div>
  <div class="social"><span class="social__dot"></span><span>@Lunavita27</span></div>
</section>

<section class="card card--back" aria-label="Retro del biglietto">
  <div class="kiwi-photo kiwi-photo--top" role="img" aria-label="Foto di kiwi tagliato a metà con foglie verdi"></div>
  <div class="kiwi-photo kiwi-photo--bottom" role="img" aria-label="Foto di kiwi tagliato a metà con foglie verdi"></div>

  <div class="brand-name">Luna Vita Chef</div>
  <div class="tagline">Sana e felice a ogni assaggio</div>

  <div class="person-name">Luna Ferraro</div>
  <ul class="contact-list">
    <li>
      <svg viewBox="0 0 16 16" aria-hidden="true"><path d="M2 5c0-2 2-3 6-3s6 1 6 3v1h-3V5H5v1H2zM4 7h8l2 7H2z"/></svg>
      <span>000-0000-0000</span>
    </li>
    <li>
      <svg viewBox="0 0 16 16" aria-hidden="true"><path d="M1 3h14v10H1zM2 4l6 5 6-5v1L8 10 2 5z" fill-rule="evenodd"/></svg>
      <span>info@piattileggeriorto.it</span>
    </li>
    <li>
      <svg viewBox="0 0 16 16" aria-hidden="true"><circle cx="8" cy="8" r="7" fill="none" stroke="#9a9a9a" stroke-width="1.4"/><path d="M1 8h14M8 1v14" stroke="#9a9a9a" stroke-width="1.2"/></svg>
      <span>www.piattileggeriorto.it</span>
    </li>
  </ul>
  <div class="vat-number">Partita IVA 01234560789</div>

  <div class="social"><span class="social__dot"></span><span>@Lunavita27</span></div>
</section>

</body>
</html>
```